Business Card Design Project

i need a bussines car design
Velora Clinical Hypnotherapy

Daniel Wexford
Psychotherapy & Hypnosis

84261937 /0427591628

back of the card appoinment space.

file was provided on a PDF, LOgo , use the blu colorsa as well , elegant, clear,

Target Market(s)

young professional, caucasian , young mothers.

Industry/Entity Type

Business

```html
<!DOCTYPE html>
<html lang="en">
<head>
<meta charset="utf-8">
<title>Velora Clinical Hypnotherapy – Business Card</title>
<link href="https://fonts.googleapis.com/css2?family=Arvo:wght@400;700&family=Raleway:wght@400&display=swap" rel="stylesheet">
<style>
  :root {
    --page: #e9eaec;
    --card: #f3f4f5;
    --blue: #1e63a8;
    --blue-mid: #4c8ec8;
    --ink: #1d1d1f;
    --grey: #6b6e73;
    --photo-a: #efe6dc;
    --photo-b: #d9c2ac;
    --badge: #c9b54a;
  }
  * { margin: 0; padding: 0; box-sizing: border-box; }
  html, body { width: 1200px; height: 800px; overflow: hidden; background: var(--page); }
  .canvas { position: relative; width: 1200px; height: 800px; }

  .card {
    position: absolute; width: 520px; height: 300px; top: 250px;
    background: var(--card);
    box-shadow: 0 8px 24px rgba(0,0,0,.12);
    overflow: hidden;
  }
  .card--front { left: 40px; }
  .card--back { left: 640px; }

  /* Front */
  .brand { position: absolute; left: 34px; top: 56px; display: flex; align-items: center; gap: 9px; white-space: nowrap; }
  .brand__dot { width: 18px; height: 18px; border-radius: 50%; background: var(--blue-mid); flex: none; }
  .brand__name { font-family: "Raleway", sans-serif; font-weight: 400; font-size: 16px; color: var(--blue); letter-spacing: .2px; }
  .brand__web { position: absolute; left: 61px; top: 82px; font-family: "Raleway", sans-serif; font-size: 9.5px; color: var(--grey); letter-spacing: .3px; white-space: nowrap; }

  .portrait {
    position: absolute; right: 0; top: 0; width: 180px; height: 300px;
    background: linear-gradient(160deg, var(--photo-a) 0%, var(--photo-b) 100%);
  }

  .contact { position: absolute; left: 34px; top: 176px; font-family: "Arvo", serif; }
  .contact__marker { position: absolute; left: -22px; top: 6px; width: 0; height: 0;
    border-top: 7px solid transparent; border-bottom: 7px solid transparent; border-right: 12px solid var(--blue); }
  .contact__name { font-weight: 700; font-size: 19px; color: var(--blue); }
  .contact__role { font-weight: 700; font-size: 11px; color: var(--ink); margin-top: 1px; }
  .contact__rows { margin-top: 12px; display: grid; gap: 4px; }
  .contact__row { display: flex; align-items: center; gap: 8px; font-weight: 700; font-size: 12px; color: var(--ink); }
  .contact__icon { width: 14px; height: 14px; background: var(--blue); border-radius: 2px; display: flex; align-items: center; justify-content: center; }

  /* Back */
  .appointments { position: absolute; left: 40px; top: 40px; font-family: "Arvo", serif; }
  .appointments__title { font-weight: 700; font-size: 18px; color: var(--blue); margin-bottom: 14px; }
  .appointments__list { list-style: none; display: grid; gap: 10px; }
  .appointments__item { display: flex; align-items: flex-end; gap: 6px; font-size: 12px; color: var(--ink); }
  .blank { display: inline-block; border-bottom: 1px solid var(--blue); height: 14px; }
  .blank--time { width: 46px; }
  .blank--day { width: 130px; }
  .blank--date { width: 26px; }
  .slash { color: var(--blue); }

  .notice { position: absolute; left: 40px; bottom: 30px; font-family: "Arvo", serif; color: var(--blue); }
  .notice__text { font-size: 9.5px; line-height: 1.45; max-width: 330px; }
  .notice__reg { font-size: 8.5px; margin-top: 8px; color: var(--grey); }
  .badge { position: absolute; left: 392px; bottom: 32px; width: 26px; height: 26px; border-radius: 50%; background: var(--badge); }
</style>
</head>
<body>
<main class="canvas">

  <section class="card card--front" aria-label="Business card front">
    <div class="brand">
      <span class="brand__dot"></span>
      <span class="brand__name">Velora Clinical Hypnotherapy</span>
    </div>
    <p class="brand__web">www.veloraclinicalhypnotherapy.com.au</p>

    <div class="portrait" role="img" aria-label="Portrait photograph of the therapist smiling, wearing glasses and a light shirt"></div>

    <div class="contact">
      <span class="contact__marker"></span>
      <p class="contact__name">Daniel Wexford</p>
      <p class="contact__role">Psychotherapy &amp; Hypnosis</p>
      <div class="contact__rows">
        <p class="contact__row">
          <span class="contact__icon">
            <svg width="9" height="9" viewBox="0 0 10 10"><path d="M2 1h2l1 2.5-1.3.8a5 5 0 0 0 2 2l.8-1.3L9 6v2c0 .6-.5 1-1 1A7 7 0 0 1 1 2c0-.5.4-1 1-1z" fill="#fff"/></svg>
          </span>84261937
        </p>
        <p class="contact__row">
          <span class="contact__icon">
            <svg width="9" height="9" viewBox="0 0 10 10"><path d="M5 1 1 4.5h1.2V9h2.2V6.5h1.2V9h2.2V4.5H9z" fill="#fff"/></svg>
          </span>48 Harlow St, Brunswick
        </p>
      </div>
    </div>
  </section>

  <section class="card card--back" aria-label="Business card back">
    <div class="appointments">
      <h2 class="appointments__title">Your Appointments</h2>
      <ol class="appointments__list">
        <li class="appointments__item">1. <span class="blank blank--time"></span>am/pm <span class="blank blank--day"></span><span class="blank blank--date"></span><span class="slash">/</span><span class="blank blank--date"></span><span class="slash">/</span><span class="blank blank--date"></span></li>
        <li class="appointments__item">2. <span class="blank blank--time"></span>am/pm <span class="blank blank--day"></span><span class="blank blank--date"></span><span class="slash">/</span><span class="blank blank--date"></span><span class="slash">/</span><span class="blank blank--date"></span></li>
        <li class="appointments__item">3. <span class="blank blank--time"></span>am/pm <span class="blank blank--day"></span><span class="blank blank--date"></span><span class="slash">/</span><span class="blank blank--date"></span><span class="slash">/</span><span class="blank blank--date"></span></li>
        <li class="appointments__item">4. <span class="blank blank--time"></span>am/pm <span class="blank blank--day"></span><span class="blank blank--date"></span><span class="slash">/</span><span class="blank blank--date"></span><span class="slash">/</span><span class="blank blank--date"></span></li>
        <li class="appointments__item">5. <span class="blank blank--time"></span>am/pm <span class="blank blank--day"></span><span class="blank blank--date"></span><span class="slash">/</span><span class="blank blank--date"></span><span class="slash">/</span><span class="blank blank--date"></span></li>
      </ol>
    </div>

    <div class="notice">
      <p class="notice__text">To reschedule your appointment please SMS or call 0427 591 628 at least 24 hours prior to your allocated time. Thank you.</p>
      <p class="notice__reg">Registration No. PRX0048215</p>
    </div>
    <span class="badge" aria-hidden="true"></span>
  </section>

</main>
</body>
</html>
```